Workshop PPT Update for AI Transformation Sessions

Our strategic consulting firm runs strategy workshops using slides as workshop exercises. These slides are used to communicate to the participants in advance, run the workshops and produce the final deliverable.

It is time for a design "upgrade". We'd like them to be more engaging, hipper and more interesting. These slides are utilitarian, so clean and usable is good. I have attached the example of what we have today. I have also attached an example of another company's slides that I like.

We can't rip off their design nor can we go away 100% from what we have. But I think it is possible to "update" our look to something closer to their look. Grey colors are fine with some color pop.

Slide styles needed are - 1) Cover Page, 2) Instructions Page, 3) Bullet list 4) Worksheet (place for participants to add content 5) Table, 6) Two column.

```html
<!DOCTYPE html>
<html lang="en">
<head>
<meta charset="utf-8">
<title>Workshop Slide Set</title>
<link href="https://fonts.googleapis.com/css2?family=Inter:wght@400;500;600;700;800&display=swap" rel="stylesheet">
<style>
  :root {
    --canvas: #c3c3c3;
    --paper: #ffffff;
    --slate: #3f4150;
    --red: #cf434b;
    --ink: #2b2b2b;
    --muted: #5a5a5a;
    --soft: #f3f3f3;
    --rule: #e3e3e3;
  }
  * { box-sizing: border-box; margin: 0; padding: 0; }
  html, body { width: 1200px; height: 1072px; overflow: hidden; background: var(--canvas); }
  body { position: relative; font-family: "Inter", Arial, sans-serif; color: var(--ink); }

  .slide { position: absolute; width: 545px; height: 306px; background: var(--paper); overflow: hidden; }
  .slide--getting-started { left: 38px; top: 45px; }
  .slide--workshop-overview { left: 618px; top: 45px; }
  .slide--kickoff { left: 38px; top: 380px; }
  .slide--creating-principles { left: 618px; top: 380px; }
  .slide--plan-structure { left: 38px; top: 721px; }
  .slide--principles-timeline { left: 618px; top: 721px; }

  .brand { position: absolute; left: 14px; top: 9px; }
  .brand__name { display: block; font-size: 13px; font-weight: 500; color: var(--slate); letter-spacing: -0.2px; line-height: 16px; }
  .brand__note { display: block; margin-left: 21px; font-size: 6.5px; font-style: italic; color: #8a8a8a; line-height: 8px; }

  .sidebar { position: absolute; left: 0; top: 42px; bottom: 0; width: 93px; background: var(--slate); color: #fff; }
  .page-no { position: absolute; right: 14px; top: 288px; font-size: 5.5px; color: var(--ink); letter-spacing: 0.2px; }

  /* Getting started */
  .sidebar__title--caps { position: absolute; left: 12px; top: 20px; font-size: 15px; font-weight: 700; line-height: 17px; letter-spacing: 0.3px; }
  .step-list { position: absolute; left: 110px; top: 65px; list-style: none; }
  .step-list li { position: relative; height: 34px; padding-left: 21px; font-size: 8.5px; line-height: 16px; color: var(--ink); }
  .step-list li::before { content: ""; position: absolute; left: 2px; top: 3px; width: 8px; height: 10px; border: 1.6px solid var(--red); border-radius: 50%; }
  .photo-frame { position: absolute; left: 313px; top: 39px; width: 225px; height: 218px; background: var(--red); }
  .photo { position: absolute; }
  .photo--meeting { left: 319px; top: 45px; width: 226px; height: 217px; background: linear-gradient(135deg, #e9e6e1 0%, #c9c2b8 45%, #8b7a6c 75%, #4a4440 100%); }

  /* Workshop overview */
  .sidebar__title--sm { position: absolute; left: 15px; top: 27px; font-size: 11px; font-weight: 600; line-height: 14px; letter-spacing: 0.3px; }
  .sidebar__meta { position: absolute; left: 16px; top: 69px; font-size: 5.8px; line-height: 11.5px; }
  .sidebar__label { position: absolute; left: 16px; top: 109px; font-size: 6.3px; font-weight: 600; }
  .tick-list { list-style: none; }
  .tick-list li { position: relative; padding-left: 8px; font-size: 4.4px; line-height: 8.5px; }
  .tick-list li::before { content: ""; position: absolute; left: 1px; top: 2.2px; width: 3.6px; height: 2px; border-left: 1px solid currentColor; border-bottom: 1px solid currentColor; transform: rotate(-45deg); }
  .sidebar .tick-list { position: absolute; left: 16px; top: 123px; }
  .flow__heading { position: absolute; left: 123px; top: 38px; font-size: 10.5px; font-weight: 600; }
  .flow__item { position: absolute; left: 123px; }
  .flow__num { position: absolute; left: 0; top: -8px; font-size: 13.5px; font-weight: 600; color: var(--red); }
  .flow__title { position: absolute; left: 32px; top: -6px; white-space: nowrap; font-size: 10.5px; font-weight: 600; color: var(--ink); }
  .flow__desc { position: absolute; left: 32px; top: 9px; white-space: nowrap; font-size: 6.5px; color: var(--muted); }

  /* Kickoff */
  .photo--boardroom { left: 93px; top: 42px; width: 452px; height: 231px; background: linear-gradient(100deg, #4c4b4b 0%, #77736e 35%, #9a958d 55%, #5b5853 78%, #3a3836 100%); }
  .cover__title { position: absolute; left: 119px; top: 110px; font-size: 26px; font-weight: 800; line-height: 31px; color: #fff; letter-spacing: 0.5px; }
  .cover__subtitle { position: absolute; left: 120px; top: 179px; font-size: 8.3px; color: #fff; }

  /* Creating principles */
  .sidebar__title--lg { position: absolute; left: 14px; top: 19px; font-size: 11px; font-weight: 600; line-height: 18px; }
  .resource-card { position: absolute; left: 125px; top: 67px; width: 172px; height: 150px; background: var(--red); color: #fff; padding-left: 27px; }
  .resource-card__head { position: absolute; left: 27px; font-size: 6.3px; font-weight: 600; }
  .resource-card__note { position: absolute; left: 27px; font-size: 4.5px; }
  .resource-card .tick-list { position: absolute; left: 27px; top: 28px; }
  .resource-card .tick-list li { line-height: 8.6px; }
  .steps { position: absolute; left: 312px; }
  .steps__num { position: absolute; left: 0; top: -7px; font-size: 11px; font-weight: 600; color: var(--red); }
  .steps__title { position: absolute; left: 27px; top: -6px; white-space: nowrap; font-size: 8.7px; font-weight: 600; color: var(--ink); }
  .steps__desc { position: absolute; left: 27px; top: 8px; white-space: nowrap; font-size: 5.2px; color: var(--muted); }

  /* Plan structure */
  .sidebar__title--plan { position: absolute; left: 16px; top: 20px; font-size: 8.8px; font-weight: 600; line-height: 17px; letter-spacing: 0.3px; }
  .plan-table { position: absolute; left: 121px; top: 61px; width: 396px; border-collapse: collapse; table-layout: fixed; }
  .plan-table th { height: 23px; background: var(--red); color: #fff; font-size: 5px; font-weight: 600; line-height: 7px; text-align: center; vertical-align: middle; }
  .plan-table td { font-size: 5.4px; line-height: 7px; text-align: center; vertical-align: top; padding-top: 8px; color: var(--ink); border-bottom: 0.6px solid var(--rule); }
  .plan-table tr:last-child td { border-bottom: 0; }
  .plan-table .col-shade { background: var(--soft); }
  .plan-table .col-level { border-right: 0.6px solid #dcdcdc; }
  .plan-table td.cell-mid { vertical-align: middle; padding-top: 0; }

  /* Principles timeline */
  .sidebar__title--tl { position: absolute; left: 12px; top: 19px; font-size: 11px; font-weight: 600; line-height: 16px; }
  .sidebar__caption { position: absolute; left: 13px; top: 53px; font-size: 4.4px; line-height: 8.5px; }
  .timeline { position: absolute; left: 0; top: 0; }
  .principle { position: absolute; width: 136px; }
  .principle--left { left: 132px; text-align: right; }
  .principle--right { left: 353px; text-align: left; }
  .principle__title { font-size: 9.8px; font-weight: 600; line-height: 12px; }
  .principle__desc { margin-top: 3px; font-size: 4.4px; line-height: 8.5px; color: var(--muted); }
</style>
</head>
<body>

<!-- Cover / getting started -->
<section class="slide slide--getting-started">
  <div class="brand"><span class="brand__name">TrueCourse</span><span class="brand__note">Copyright</span></div>
  <div class="sidebar"><h2 class="sidebar__title--caps">GETTING<br>STARTED</h2></div>
  <ul class="step-list">
    <li>Complete the Engagement Sizing Survey.</li>
    <li>Collect relevant inputs.</li>
    <li>Determine workshop participants &amp; date.</li>
    <li>Send invites, to include pre-work.</li>
  </ul>
  <div class="photo-frame"></div>
  <div class="photo photo--meeting" role="img" aria-label="Photo of a facilitator presenting charts on a flip board to a seated team with laptops"></div>
  <span class="page-no">PAGE NO : 01</span>
</section>

<!-- Workshop overview -->
<section class="slide slide--workshop-overview">
  <div class="brand"><span class="brand__name">TrueCourse</span><span class="brand__note">Copyright</span></div>
  <div class="sidebar">
    <h2 class="sidebar__title--sm">WORKSHOP<br>OVERVIEW</h2>
    <p class="sidebar__meta">Participants: Execs<br>Duration:&nbsp; 2 hrs.</p>
    <p class="sidebar__label">Prep Work:</p>
    <ul class="tick-list">
      <li>Org Strategy</li>
      <li>2023 Goal Performance</li>
      <li>Existing policies</li>
      <li>Pre-thinking questions</li>
    </ul>
  </div>
  <h3 class="flow__heading">Workshop Flow</h3>
  <div class="flow__item" style="top:71px"><span class="flow__num">01</span><span class="flow__title">Confirm Company Direction</span><span class="flow__desc">Recap organizational purpose, values, vision &amp; winning strategy.</span></div>
  <div class="flow__item" style="top:108px"><span class="flow__num">02</span><span class="flow__title">Develop AI Vision</span></div>
  <div class="flow__item" style="top:133px"><span class="flow__num">03</span><span class="flow__title">Develop AI Guiding Principles</span><span class="flow__desc">Developed AI Guiding Principles, supporting policies to include approved tools.</span></div>
  <div class="flow__item" style="top:173px"><span class="flow__num">04</span><span class="flow__title">Agree on a Governance Approach</span><span class="flow__desc">Agreed upon governance approach, structure, &amp; executive champion.</span></div>
  <div class="flow__item" style="top:215px"><span class="flow__num">05</span><span class="flow__title">Agree on a Training &amp; Learning Approach</span><span class="flow__desc">Set approach to training &amp; continuous learning.</span></div>
  <div class="flow__item" style="top:255px"><span class="flow__num">06</span><span class="flow__title">Determine Rollout &amp; Communication</span><span class="flow__desc">Organizational rollout &amp; continuous communication.</span></div>
  <span class="page-no">PAGE NO : 04</span>
</section>

<!-- Kickoff cover -->
<section class="slide slide--kickoff">
  <div class="brand"><span class="brand__name">TrueCourse</span><span class="brand__note">Copyright</span></div>
  <div class="sidebar"></div>
  <div class="photo photo--boardroom" role="img" aria-label="Photo of a team meeting around a boardroom table in front of tall city windows"></div>
  <h1 class="cover__title">KICKOFF &amp;<br>DISCOVERY</h1>
  <p class="cover__subtitle">Sizing &amp; Scoping AI Transformation</p>
  <span class="page-no">PAGE NO : 02</span>
</section>

<!-- Creating principles -->
<section class="slide slide--creating-principles">
  <div class="brand"><span class="brand__name">TrueCourse</span><span class="brand__note">Copyright</span></div>
  <div class="sidebar"><h2 class="sidebar__title--lg">Creating your<br>AI Guiding<br>Principles</h2></div>
  <div class="resource-card">
    <span class="resource-card__head" style="top:15px">Your Existing Material</span>
    <ul class="tick-list">
      <li>Company Values</li>
      <li>Current Policies (GDPR, CCPA, etc.)</li>
      <li>Legal Guidance</li>
      <li>OTHER</li>
    </ul>
    <span class="resource-card__head" style="top:77px">Examples for Inspiration</span>
    <span class="resource-card__note" style="top:93px">See next slides</span>
    <span class="resource-card__head" style="top:114px">AI Assistant Prompts</span>
    <span class="resource-card__note" style="top:130px">HERE</span>
  </div>
  <div class="steps" style="top:82px"><span class="steps__num">01</span><span class="steps__title">Create the Outline</span><span class="steps__desc">Determine the topics that need a principle.</span></div>
  <div class="steps" style="top:114px"><span class="steps__num">02</span><span class="steps__title">Audit the Outline</span><span class="steps__desc">Look at the current policies to determine if all topics are covered.</span></div>
  <div class="steps" style="top:144px"><span class="steps__num">03</span><span class="steps__title">Draft the Guiding Principles.</span></div>
  <div class="steps" style="top:163px"><span class="steps__num">04</span><span class="steps__title">Determine which GPs need detailed policies.</span></div>
  <div class="steps" style="top:184px"><span class="steps__num">05</span><span class="steps__title">Determine which AI Tools support the GPs.</span></div>
  <div class="steps" style="top:205px"><span class="steps__num">06</span><span class="steps__title">Finalize via a legal and executive review</span></div>
  <span class="page-no">PAGE NO : 05</span>
</section>

<!-- Plan structure table -->
<section class="slide slide--plan-structure">
  <div class="brand"><span class="brand__name">TrueCourse</span><span class="brand__note">Copyright</span></div>
  <div class="sidebar"><h2 class="sidebar__title--plan">PLAN<br>STRUCTURE</h2></div>
  <table class="plan-table">
    <colgroup><col style="width:49px"><col style="width:50px"><col style="width:99px"><col style="width:99px"><col style="width:99px"></colgroup>
    <thead>
      <tr><th colspan="2">LEVEL</th><th>PLANNING ELEMENT<br>&amp; DEFINITION</th><th>ACCOUNTABILITY/OWNER</th><th>FREQUENCY OF MODIFICATION</th></tr>
    </thead>
    <tbody>
      <tr style="height:41px"><td class="col-shade col-level">1</td><td class="col-shade">What<br>(Overall)</td><td>Strategic Priorities</td><td class="col-shade">N/A</td><td>3+ years</td></tr>
      <tr style="height:50px"><td class="col-shade col-level">1.1</td><td class="col-shade">What<br>(Overall)</td><td>Goals<br>Outcomes &amp; Strategies</td><td class="col-shade">Executive Leadership</td><td>1-3 years</td></tr>
      <tr style="height:46px"><td class="col-shade col-level">1.1.1</td><td class="col-shade cell-mid" rowspan="2">How</td><td>Key Performance Indicators<br>and /or Intiatives</td><td class="col-shade"></td><td>1 year<br>(w/ qrtly targets)</td></tr>
      <tr style="height:40px"><td class="col-shade col-level">1.1.1.1</td><td>Action Items</td><td class="col-shade"></td><td>Quarterly / Monthly</td></tr>
    </tbody>
  </table>
  <span class="page-no">PAGE NO : 03</span>
</section>

<!-- Principles timeline -->
<section class="slide slide--principles-timeline">
  <div class="brand"><span class="brand__name">TrueCourse</span><span class="brand__note">Copyright</span></div>
  <div class="sidebar">
    <h2 class="sidebar__title--tl">AI Guiding<br>Principles</h2>
    <p class="sidebar__caption">What guides our decision-making<br>and approach?</p>
  </div>
  <svg class="timeline" width="545" height="306" viewBox="0 0 545 306" aria-hidden="true">
    <path d="M293 44 V239 A18.5 18.5 0 0 0 330 239 V44" fill="none" stroke="#3f4150" stroke-width="1.6"/>
    <g fill="#cf434b">
      <circle cx="293" cy="71" r="12.5"/><circle cx="293" cy="149" r="12.5"/><circle cx="293" cy="227" r="12.5"/>
      <circle cx="330" cy="110" r="12.5"/><circle cx="330" cy="189" r="12.5"/>
    </g>
    <g fill="none" stroke="#fff" stroke-width="1.8" stroke-linecap="round" stroke-linejoin="round">
      <path d="M288.5 71 l3 3 l6 -6"/><path d="M288.5 149 l3 3 l6 -6"/><path d="M288.5 227 l3 3 l6 -6"/>
      <path d="M325.5 110 l3 3 l6 -6"/><path d="M325.5 189 l3 3 l6 -6"/>
    </g>
  </svg>
  <div class="principle principle--left" style="top:59px"><p class="principle__title">Principle #1</p><p class="principle__desc">Complete perspective from Executives, Directors, Managers &amp; Staff. Conduct competitive analysis and customer research (optional).</p></div>
  <div class="principle principle--left" style="top:137px"><p class="principle__title">Principle #2</p><p class="principle__desc">Complete perspective from Executives, Directors, Managers &amp; Staff. Conduct competitive analysis and customer research (optional).</p></div>
  <div class="principle principle--left" style="top:215px"><p class="principle__title">Principle #3</p><p class="principle__desc">Complete perspective from Executives, Directors, Managers &amp; Staff. Conduct competitive analysis and customer research (optional).</p></div>
  <div class="principle principle--right" style="top:98px"><p class="principle__title">Principle #4</p><p class="principle__desc">Complete perspective from Executives, Directors, Managers &amp; Staff. Conduct competitive analysis and customer research (optional).</p></div>
  <div class="principle principle--right" style="top:177px"><p class="principle__title">Principle #5</p><p class="principle__desc">Complete perspective from Executives, Directors, Managers &amp; Staff. Conduct competitive analysis and customer research (optional).</p></div>
  <span class="page-no">PAGE NO : 06</span>
</section>

</body>
</html>
```